Harbor Loom Floors Letterhead

Letterhead used for business reasons. It must be editable and easy to use.

Address is 2715 W. Pelican Lane Englewood FL 34187 - 941.382.6519

```html
<!DOCTYPE html>
<html lang="en">
<head>
<meta charset="utf-8">
<title>Harbor Loom Floors Letterhead</title>
<link href="https://fonts.googleapis.com/css2?family=Lato:wght@400;700&family=Montserrat:wght@400&family=Italianno&display=swap" rel="stylesheet">
<style>
  :root {
    --brand-orange: #e08e2b;
    --brand-taupe: #978d87;
    --ink: #1c1c1c;
    --paper: #ffffff;
    --backdrop: #e4e4e4;
  }
  html, body {
    margin: 0;
    padding: 0;
    width: 1174px;
    height: 1200px;
    overflow: hidden;
    background: var(--backdrop);
  }
  .letterhead {
    position: absolute;
    left: 142px;
    top: 25px;
    width: 889px;
    height: 1150px;
    background: var(--paper);
    font-family: 'Lato', sans-serif;
    color: var(--ink);
  }
  .brand-name {
    position: absolute;
    left: 55px;
    top: 82px;
    margin: 0;
    font-family: 'Lato', sans-serif;
    font-weight: 700;
    font-size: 46px;
    line-height: 1;
    color: var(--brand-orange);
    letter-spacing: 0.5px;
  }
  .contact {
    position: absolute;
    right: 56px;
    top: 70px;
    font-family: 'Montserrat', sans-serif;
    font-size: 15px;
    line-height: 20px;
    color: #3a3a3a;
    text-align: left;
  }
  .contact p { margin: 0; }
  .contact .phone {
    margin-top: 11px;
    display: flex;
    align-items: center;
    gap: 7px;
    margin-left: -3px;
  }
  .contact .phone svg { width: 13px; height: 13px; }
  .header-rule {
    position: absolute;
    left: 55px;
    top: 183px;
    width: 778px;
    height: 2px;
    background: var(--brand-orange);
  }
  .letter-body {
    position: absolute;
    left: 55px;
    top: 252px;
    width: 778px;
    font-size: 17.3px;
    line-height: 20px;
  }
  .letter-body p { margin: 0; }
  .date { margin-bottom: 22px !important; }
  .recipient { margin-bottom: 45px !important; }
  .company { margin-bottom: 41px !important; }
  .salutation {
    font-weight: 700;
    font-size: 22px;
    margin-bottom: 42px !important;
  }
  .paragraph {
    text-align: justify;
    line-height: 19.3px;
    margin-bottom: 18px !important;
  }
  .closing { margin-top: 42px !important; }
  .signature {
    margin-top: 52px !important;
    font-family: 'Italianno', cursive;
    font-size: 48px;
    line-height: 1;
  }
  .footer-band {
    position: absolute;
    bottom: 0;
    height: 19px;
  }
  .footer-band.primary { left: 0; width: 607px; background: var(--brand-orange); }
  .footer-band.secondary { left: 616px; right: 0; background: var(--brand-taupe); }
</style>
</head>
<body>
  <main class="letterhead">
    <h1 class="brand-name">Harbor Loom Floors</h1>

    <address class="contact">
      <p>2715 W. Pelican Lane</p>
      <p>Englewood FL 34187</p>
      <p class="phone">
        <svg viewBox="0 0 24 24" aria-hidden="true"><path fill="#e08e2b" d="M6.6 10.8c1.4 2.8 3.8 5.1 6.6 6.6l2.2-2.2c.3-.3.7-.4 1-.2 1.1.4 2.3.6 3.6.6.6 0 1 .4 1 1V20c0 .6-.4 1-1 1C10.6 21 3 13.4 3 4c0-.6.4-1 1-1h3.5c.6 0 1 .4 1 1 0 1.3.2 2.5.6 3.6.1.3 0 .7-.2 1z"/><path fill="none" stroke="#e08e2b" stroke-width="1.8" stroke-linecap="round" d="M14 3.5a7 7 0 0 1 6.5 6.5M14 7a3.5 3.5 0 0 1 3 3"/></svg>
        941.382.6519
      </p>
    </address>

    <div class="header-rule"></div>

    <section class="letter-body">
      <p class="date">January-03-2020</p>
      <p class="recipient">Mr, John Doe<br>President</p>
      <p class="company">Northgate Corporation<br>123 Street Name, Suite# 10<br>City, State, 120023</p>
      <p class="salutation">Dear Mr, John</p>
      <p class="paragraph">Lorem ipsum dolor sit amet, consectetur adipiscing elit, sed do eiusmod tempor incididunt ut labore et dolore magna aliqua. Ut enim ad minim veniam, quis nostrud exercitation ullamco laboris nisi ut aliquip ex ea commodo consequat. Duis aute irure dolor in reprehenderit in voluptate velit esse cillum dolore eu fugiat nulla pariatur.</p>
      <p class="paragraph">Lorem ipsum dolor sit amet, consectetur adipiscing elit, sed do eiusmod tempor incididunt ut labore et dolore magna aliqua. Ut enim ad minim veniam, quis nostrud exercitation ullamco laboris nisi ut aliquip ex ea commodo consequat. Duis aute irure dolor in reprehenderit in voluptate velit esse cillum dolore eu fugiat nulla pariatur.</p>
      <p class="paragraph">Lorem ipsum dolor sit amet, consectetur adipiscing elit, sed do eiusmod tempor incididunt ut labore et dolore magna aliqua. Ut enim ad minim veniam, quis nostrud exercitation ullamco laboris nisi ut aliquip ex ea commodo consequat.</p>
      <p class="paragraph">Excepteur sint occaecat cupidatat non proident, sunt in culpa qui officia deserunt mollit anim id est laborum. re et dolore magnam aliquam quaerat voluptatem.</p>
      <p class="closing">Regards</p>
      <p class="signature">Dana Whitfield</p>
    </section>

    <div class="footer-band primary"></div>
    <div class="footer-band secondary"></div>
  </main>
</body>
</html>
```